Bestselling author requires book cover for sequel

I need a book cover design for a sequel to Vinegar Before Gravy (see Quillmarket.co.uk) that maintains a little bit of continuity with the original, humo(u)r, a SUBTLE element of 'British holidaymaker in Spain/Tenerife/sub-tropical island' and will work for both ebook and print.
The most important thing is that the book will stand out in a crowd.
Use the same title at the moment (Vinegar Before Gravy: Tales of a Harbourside Deckhand), but this will change according to the design.

Requirements
Must have
• Cover must have humour and some continuity with the first book, Vinegar Before Gravy.
Bear in mind the continuity doesn't have to be in using the same or similar image, it could just be in the font used.
A lot of the designs so far are just alternative images of a British man abroad. I need something more 'subtle'/clever to suggest Brit abroad.
Should not have
• References to the 'Tales' bit of the title. It's a humorous travel narrative, not a sordid 'tell-all'.

```html
<!DOCTYPE html>
<html lang="en">
<head>
<meta charset="utf-8">
<title>Vinegar Before Gravy — Cover Wrap</title>
<link rel="stylesheet" href="https://fonts.googleapis.com/css2?family=Tinos:wght@400;700&display=swap">
<style>
  :root {
    --canvas: #e9e9ea;
    --cover-blue: #a6bccb;
    --back-blue: #9fb4c4;
    --sky-top: #a9c4d7;
    --sky-mid: #b9ccd8;
    --shore: #c9c2b4;
    --sand: #b9a994;
    --sand-deep: #a8977f;
    --castle-light: #a08a6c;
    --castle-dark: #7d6a52;
    --title-red: #e0141b;
    --navy: #1f2960;
    --box-red: #c8090f;
    --white: #ffffff;
  }
  * { box-sizing: border-box; margin: 0; padding: 0; }
  html, body {
    width: 1200px; height: 800px; overflow: hidden;
    background: var(--canvas);
    font-family: "Tinos", "Times New Roman", serif;
  }
  .cover-wrap {
    position: absolute; left: 200px; top: 100px;
    width: 800px; height: 600px;
    display: flex;
    box-shadow: 0 8px 24px rgba(0,0,0,0.18);
  }
  /* Back cover */
  .back-cover {
    width: 385px; height: 100%;
    background: var(--back-blue);
    padding: 24px 30px 24px;
    display: flex; flex-direction: column; align-items: center;
  }
  .back-author {
    font-size: 10px; font-weight: 700; color: var(--navy);
    letter-spacing: 0.3px;
  }
  .back-title {
    color: var(--title-red); font-weight: 700;
    font-size: 34px; line-height: 1; text-align: center;
    margin-top: 2px;
  }
  .back-subtitle {
    color: var(--navy); font-weight: 700; font-size: 12px;
    margin-top: 5px; text-align: center;
  }
  .back-blurb {
    color: var(--navy); font-size: 11px; line-height: 1.18;
    text-align: justify; text-align-last: center;
    margin-top: 16px;
  }
  .back-footer {
    margin-top: auto; width: 100%;
    display: flex; justify-content: space-between;
  }
  .placeholder-box {
    width: 106px; height: 46px; background: var(--box-red);
    color: var(--white); font-size: 11px;
    display: flex; align-items: center; justify-content: center;
  }
  /* Spine */
  .spine {
    width: 30px; height: 100%;
    background: var(--cover-blue);
    border-left: 1px solid rgba(0,0,0,0.08);
    border-right: 1px solid rgba(0,0,0,0.12);
    display: flex; flex-direction: column; align-items: center;
    padding: 20px 0 16px;
  }
  .spine-title, .spine-author {
    writing-mode: vertical-rl; white-space: nowrap; font-weight: 700;
  }
  .spine-title { color: var(--title-red); font-size: 20px; letter-spacing: 1px; }
  .spine-author { color: var(--navy); font-size: 8px; margin-top: auto; }
  /* Front cover */
  .front-cover {
    position: relative; width: 385px; height: 100%;
    overflow: hidden;
  }
  .front-backdrop {
    position: absolute; inset: 0;
    background: linear-gradient(to bottom,
      var(--sky-top) 0%, var(--sky-mid) 46%,
      var(--shore) 56%, var(--sand) 78%, var(--sand-deep) 100%);
  }
  .front-subject {
    position: absolute; left: 125px; top: 240px;
    width: 165px; height: 335px;
    border-radius: 6px;
    background: linear-gradient(to bottom,
      rgba(160,138,108,0.35) 0%, var(--castle-light) 45%, var(--castle-dark) 100%);
  }
  .front-text {
    position: relative; text-align: center; padding-top: 16px;
  }
  .front-title {
    color: var(--title-red); font-weight: 700;
    font-size: 50px; line-height: 0.98;
  }
  .front-subtitle {
    color: var(--navy); font-weight: 700;
    font-size: 24px; line-height: 1.12; margin-top: 8px;
  }
  .front-author {
    color: var(--navy); font-weight: 700; font-size: 15px; margin-top: 6px;
  }
</style>
</head>
<body>
  <main class="cover-wrap">
    <section class="back-cover">
      <div class="back-author">TOM HADLEY'S</div>
      <h2 class="back-title">VINEGAR<br>BEFORE<br>GRAVY</h2>
      <div class="back-subtitle">TALES OF A HARBOURSIDE DECKHAND</div>
      <p class="back-blurb">Lorem ipsum dolor sit amet, consectetur adipisicing elit, sed do eiusmod tempor incididunt ut labore et dolore magna aliqua. Ut enim ad minim veniam, quis nostrud exercitation. Lorem ipsum dolor sit amet, consectetur adipisicing elit, sed do eiusmod tempor incididunt ut labore et dolore magna aliqua. Ut enim ad minim veniam, quis nostrud exercitation. Lorem ipsum dolor sit amet, consectetur adipisicing elit, sed do eiusmod tempor incididunt ut labore et dolore magna aliqua. Ut enim ad minim veniam, quis nostrud exercitation. Lorem ipsum dolor sit amet, consectetur adipisicing elit, sed do eiusmod tempor incididunt ut labore et dolore magna aliqua. Ut enim ad minim veniam, quis nostrud exercitation. Lorem ipsum dolor sit amet, consectetur adipisicing elit, sed do eiusmod tempor incididunt ut labore et dolore magna aliqua. Ut enim ad minim veniam, quis nostrud exercitation. Lorem ipsum dolor sit amet, consectetur adipisicing elit, sed do eiusmod tempor incididunt ut labore et dolore magna aliqua. Ut enim ad minim veniam, quis nostrud exercitation. Lorem ipsum dolor sit amet, consectetur adipisicing elit, sed do eiusmod tempor incididunt ut labore et dolore magna aliqua. Ut enim ad minim veniam, quis nostrud exercitation. Lorem ipsum dolor sit amet, consectetur adipisicing elit, sed do eiusmod tempor incididunt ut labore et dolore magna aliqua. Ut enim ad minim veniam, quis nostrud exercitation.</p>
      <div class="back-footer">
        <div class="placeholder-box">LOGO</div>
        <div class="placeholder-box">ISBN</div>
      </div>
    </section>

    <section class="spine">
      <div class="spine-title">VINEGAR BEFORE GRAVY</div>
      <div class="spine-author">TOM HADLEY</div>
    </section>

    <section class="front-cover">
      <div class="front-backdrop" role="img" aria-label="Photograph background: soft blue sea and sky over a sandy beach"></div>
      <div class="front-subject" role="img" aria-label="Photograph of a small stacked sandcastle on the beach topped with a little British flag on a wooden stick"></div>
      <div class="front-text">
        <h1 class="front-title">VINEGAR<br>BEFORE<br>GRAVY</h1>
        <div class="front-subtitle">TALES OF A<br>HARBOURSIDE DECKHAND</div>
        <div class="front-author">BY TOM HADLEY</div>
      </div>
    </section>
  </main>
</body>
</html>
```